Its time for a new website

We are at a point now where we are in desperate need of a new website. It was last updated 2006 but still looks like its 1995. We are looking for something eye catching to our clients but easy to navigate and add/remove photos of jobs/trucks and information. Our key business is the manufacture of fire appliances and resale of parts and equipment.

www.kestrelrigs.com.au

Coding

Coded - Design and coding required

Number of Pages Required

5+ page

Requirements
Must have
• Logo

```html
<!DOCTYPE html>
<html lang="en">
<head>
<meta charset="utf-8">
<title>Kestrel Rigs – Fire Appliances</title>
<link rel="stylesheet" href="https://fonts.googleapis.com/css2?family=Hind:wght@400;500;600;700&display=swap">
<style>
:root{
  --dark:#241a17;
  --darker:#1a1311;
  --red:#e3000f;
  --red-deep:#b30009;
  --ink:#1d1d1d;
  --muted:#8a8a8a;
  --panel:#f2f2f2;
  --white:#ffffff;
  --brand-blue:#2f8fd8;
}
*{box-sizing:border-box;margin:0;padding:0}
html,body{width:730px;height:1200px;overflow:hidden;background:var(--white)}
body{position:relative;font-family:"Hind",Arial,sans-serif;color:var(--ink)}
.abs{position:absolute}

/* header */
.site-header{left:0;top:0;width:730px;height:88px;background:var(--dark)}
.brand{position:absolute;left:60px;top:31px;display:flex;align-items:center;gap:8px}
.brand-dot{width:26px;height:26px;border-radius:50%;background:var(--red)}
.brand-name{font-size:17px;font-weight:600;color:var(--brand-blue);line-height:1}
.search{left:532px;top:42px;width:137px;height:28px;background:linear-gradient(#f4f4f4,#c9c9c9);display:flex;align-items:center;padding-left:10px;gap:6px;font-size:8px;color:#333}

/* navigation */
.main-nav{left:0;top:88px;width:730px;height:32px;background:linear-gradient(#f0101b,#c4000a)}
.main-nav a{position:absolute;top:0;height:32px;line-height:33px;color:var(--white);font-size:10px;text-decoration:none;text-transform:uppercase;white-space:nowrap}
.nav-sep{position:absolute;top:0;width:1px;height:32px;background:rgba(255,255,255,.35)}

/* hero */
.hero{left:0;top:120px;width:730px;height:286px;background:radial-gradient(ellipse at 35% 20%,#fbe7a8 0%,#f3a046 25%,#c9561d 50%,#5a2613 80%,#2a1410 100%)}
.hero-panel{left:60px;top:174px;width:260px;height:160px;background:rgba(70,60,55,.85);padding:22px 25px}
.hero-panel h1{font-size:24px;font-weight:400;color:var(--white);line-height:1}
.hero-panel p{margin-top:14px;font-size:7px;line-height:12px;color:#ddd}
.btn{display:inline-block;background:linear-gradient(#ee1420,#b8000a);color:var(--white);text-decoration:none;border-radius:2px}
.hero-panel .btn{margin-top:16px;width:73px;height:31px;line-height:32px;text-align:center;font-size:9.5px}
.dots{left:343px;top:377px;display:flex;gap:10px}
.dots span{width:9px;height:9px;border-radius:50%;background:#444}
.dots span.on{background:var(--red)}

/* section headings */
.sec-title{font-size:22px;font-weight:700;line-height:1;text-transform:uppercase;letter-spacing:-.2px;white-space:nowrap}
.sec-title em{font-style:normal;color:var(--red)}
.rule{height:1px;background:#e08080}
.arrow-box{width:25px;height:25px;background:#1e1613;color:var(--white);font-size:11px;text-align:center;line-height:26px}

/* products */
.product{top:498px;width:146px}
.product-photo{height:110px;border-bottom:2px solid var(--red)}
.product h3{margin-top:20px;font-size:16px;font-weight:700;text-transform:uppercase;line-height:1}
.product p{margin-top:9px;font-size:7.5px;line-height:12.4px;color:var(--muted)}
.product .btn{margin-top:14px;width:65px;height:29px;line-height:30px;text-align:center;font-size:7.5px}

/* welcome */
.welcome-text{left:60px;top:836px;width:222px;font-size:7.5px;line-height:12.4px;color:var(--muted)}
.welcome-text p+p{margin-top:12.4px}
.welcome-photo{left:290px;top:836px;width:140px;height:92px;background:linear-gradient(#c9ced6,#9aa3ad 55%,#7d7a6a)}
.welcome-link{left:290px;top:928px;width:140px;height:28px;background:var(--red);color:var(--white);font-size:10px;text-align:center;line-height:29px}

/* news */
.news-card{left:448px;top:838px;width:221px;height:118px;background:var(--panel);border-bottom:2px solid var(--red)}
.news-thumb{left:13px;top:12px;width:65px;height:52px;background:linear-gradient(#c33a2e,#8f2018 60%,#6b6f60)}
.news-title{left:87px;top:16px;font-size:12.5px;line-height:15px;color:var(--red);text-transform:uppercase}
.news-date{left:87px;top:55px;font-size:7.5px;color:#666}
.news-body{left:13px;top:73px;width:200px;font-size:7.5px;line-height:12.4px;color:#666}

/* footer */
.site-footer{left:0;top:995px;width:730px;height:155px;background:var(--dark)}
.foot-col{top:1022px}
.foot-col h4{font-size:16px;font-weight:600;color:var(--white);text-transform:uppercase;line-height:1}
.foot-col ul{list-style:none;margin-top:10px}
.foot-col li{font-size:7.5px;line-height:12.4px;color:#aaa;white-space:nowrap}
.social li{display:flex;align-items:center;gap:8px;line-height:21.6px}
.social i{display:block;width:12px;height:12px;border-radius:50%;background:#e6e6e6}
.copyright{left:0;top:1150px;width:730px;height:50px;background:var(--darker);text-align:center;line-height:52px;font-size:7.5px;color:#aaa}
</style>
</head>
<body>

<header class="abs site-header">
  <div class="brand">
    <span class="brand-dot"></span>
    <span class="brand-name">Kestrel Rigs</span>
  </div>
  <div class="abs search">
    <svg width="9" height="9" viewBox="0 0 10 10"><circle cx="4" cy="4" r="3" fill="none" stroke="#222" stroke-width="1.6"/><line x1="6.3" y1="6.3" x2="9.3" y2="9.3" stroke="#222" stroke-width="1.6"/></svg>
    Search
  </div>
</header>

<nav class="abs main-nav">
  <a style="left:60px">Home</a><span class="nav-sep" style="left:102px"></span>
  <a style="left:117px">About us</a><span class="nav-sep" style="left:178px"></span>
  <a style="left:193px">Pumpers</a><span class="nav-sep" style="left:253px"></span>
  <a style="left:265px">Tankers</a><span class="nav-sep" style="left:321px"></span>
  <a style="left:334px">GPA/Rescue</a><span class="nav-sep" style="left:406px"></span>
  <a style="left:421px">Light Tankers</a><span class="nav-sep" style="left:506px"></span>
  <a style="left:522px">Trailers</a><span class="nav-sep" style="left:576px"></span>
  <a style="left:590px">Slip-on units</a>
</nav>

<section class="abs hero" role="img" aria-label="Firefighter in breathing apparatus spraying a hose against a wall of flames"></section>
<div class="abs hero-panel">
  <h1>Fire Appliances</h1>
  <p>Appliances manufacture quality fire truck and tender units in the South West region of Australia</p>
  <a class="btn">Read More</a>
</div>
<div class="abs dots"><span></span><span class="on"></span><span></span></div>

<h2 class="abs sec-title" style="left:60px;top:440px">Our <em>Product</em></h2>
<div class="abs arrow-box" style="left:618px;top:438px">&#8249;</div>
<div class="abs arrow-box" style="left:644px;top:438px">&#8250;</div>
<div class="abs rule" style="left:60px;top:478px;width:609px"></div>

<article class="abs product" style="left:60px">
  <div class="product-photo" role="img" aria-label="Red pumper fire truck" style="background:linear-gradient(#b9c3cc,#c8321f 45%,#8a1a12 80%,#6a6a66)"></div>
  <h3>Pumpers</h3>
  <p>Kestrel Rigs are Western Australia's Largest, most experienced and competent manufacturer</p>
  <a class="btn">Read More</a>
</article>
<article class="abs product" style="left:214px">
  <div class="product-photo" role="img" aria-label="Red water tanker truck" style="background:linear-gradient(#c5ccd2,#b8312a 50%,#7c2a22 80%,#777)"></div>
  <h3>Tankers</h3>
  <p>Kestrel Rigs are Western Australia's Largest, most experienced and competent manufacturer</p>
  <a class="btn">Read More</a>
</article>
<article class="abs product" style="left:370px">
  <div class="product-photo" role="img" aria-label="Red rescue appliance with open equipment lockers" style="background:linear-gradient(#3a2a2a,#d32a22 40%,#a5a5a5 70%,#2a2a2a)"></div>
  <h3>GPA / Rescue</h3>
  <p>Kestrel Rigs are Western Australia's Largest, most experienced and competent manufacturer</p>
  <a class="btn">Read More</a>
</article>
<article class="abs product" style="left:524px">
  <div class="product-photo" role="img" aria-label="White light rescue utility vehicle" style="background:linear-gradient(#9fb0bf,#e8e8e8 45%,#cfcfcf 75%,#9a8f78)"></div>
  <h3>GPA / Rescue</h3>
  <p>Kestrel Rigs are Western Australia's Largest, most experienced and competent manufacturer</p>
  <a class="btn">Read More</a>
</article>

<h2 class="abs sec-title" style="left:60px;top:774px">Welcome to <em>Kestrel</em></h2>
<div class="abs rule" style="left:60px;top:816px;width:368px"></div>
<h2 class="abs sec-title" style="left:446px;top:774px">Latest <em>News</em></h2>
<svg class="abs" style="left:654px;top:778px" width="15" height="11" viewBox="0 0 15 11"><polyline points="5,1 1,5.5 5,10" fill="none" stroke="#222" stroke-width="1.4"/><polyline points="10,1 14,5.5 10,10" fill="none" stroke="#222" stroke-width="1.4"/></svg>
<div class="abs rule" style="left:447px;top:816px;width:222px"></div>

<div class="abs welcome-text">
  <p>Fire-Brigade Captain and 35-year veteran volunteer Fire-fighter, Martin Doyle, established Kestrel Rigs in 1988. As a fully Qualified automotive motor mechanic, he has gained the necessary experience and expertise required to develop an ever increasing range of high Quality, Functional and Affordable fire appliances suited to the harsh Australian environment.</p>
  <p>Kestrel Rigs has grown from a one-man operation, to the Prestigious, Thriving and Exciting business it is today, employing fifteen permanent, enthusiastic staff.</p>
</div>
<div class="abs welcome-photo" role="img" aria-label="Blue water trailer with a red monitor nozzle in a paddock"></div>
<div class="abs welcome-link">more about company</div>

<div class="abs news-card">
  <div class="abs news-thumb" role="img" aria-label="Red firefighting trailer unit"></div>
  <div class="abs news-title">For all your fire<br>fighting needs</div>
  <div class="abs news-date">May 27,2015</div>
  <div class="abs news-body">Fire-Brigade Captain and 35-year veteran volunteer Fire-fighter, Martin Doyle, established</div>
</div>

<footer class="abs site-footer"></footer>
<div class="abs foot-col" style="left:60px">
  <h4>Company</h4>
  <ul><li>Home</li><li>About us</li><li>News</li><li>Careers</li><li>Contact Us</li></ul>
</div>
<div class="abs foot-col" style="left:226px">
  <h4>Products</h4>
  <ul><li>Pumpers</li><li>Tankers</li><li>GPA/Rescue</li><li>Light Tankers</li><li>Trailers</li><li>Slip-on Units</li></ul>
</div>
<div class="abs foot-col" style="left:388px">
  <h4>Address</h4>
  <ul><li>Lot 14 Banksia Road Yarralup 6399</li><li>Western Australia</li><li>&nbsp;</li><li>Phone 08 9555 0174</li><li>Fax 08 9555 0160</li></ul>
</div>
<div class="abs foot-col social" style="left:582px">
  <h4>Follow us</h4>
  <ul style="margin-top:6px"><li><i></i>Community Page</li><li><i></i>Quick Updates</li><li><i></i>Video Channel</li></ul>
</div>
<div class="abs copyright">© 2015 kestrelrigs.com.au. All rights reserved.</div>

</body>
</html>
```